Jewelry Manufacturing & Repair business needs advertising mailout - 9x4 flyer

Need new double sided flyer designed for an insert into a mailout. Want 9x4 (vertical design) to fit in 9.5" x 4.125" envelopes. Company based out of Louisiana called "Lem Vossick Manufacturing." Been in business for 45 years. We specialize in custom jewelry design and casting on the wholesale level. We are a full service trade shop offering CAD design, casting services, basic and advanced jewelry repair. Most of our customers are drawn to the fact that they talk directly with the owner/designer of the company each time they call. I've attached several images of CAD renders we've built and of our logo. I've also attached a copy of an old mailout we sent out 10 years ago that I designed myself (and it needed a lot of work). The business information listed in this old mailout is correct, except that we’ve been in business 45 years now. I would like the final design to be "business bold," portraying business strength and stability. I like shades of blue, or a gold/silver color scheme. Logo is black and white. Need double sided.

Looking for project to be less wordy than the 10 yr old mailout. Don’t need the “example scenario” in this flyer.

The weekend has made the 2 day timeframe very tight. Would like to extend timeframe, but I will select a design on Monday at 3:00 pm (USA Central time).

Target Market(s)

Retail Jewelry Stores

Industry/Entity Type

Jewelry

Colors
cfdeed
0455a3
3176b5
85acd3

Requirements
Must have
• All contact information.
Nice to have
• Purpose of this flyer is to get new accounts for our business. We want something that the retail jewelry store will notice something that will make them not throw away immediately, but instead hold onto for the future.
• This upcoming Christmas season is usually very busy for retail stores, so we can help take some of the overflow of work and still meet deadlines. With our help, they shouldn't have to turn any customer away.
Should not have
• We will be partnering in this mailout with a sister wholesale diamond company. Therefore, we don't want to mention that our company sells any diamonds, as we want to leave that part up to our sister company.

```html
<!DOCTYPE html>
<html lang="en">
<head>
<meta charset="utf-8">
<title>Lem Vossick Manufacturing – Trade Shop Flyer</title>
<link rel="stylesheet" href="https://fonts.googleapis.com/css2?family=Cinzel:wght@400;600;700&family=Lora:wght@400;600;700&display=swap">
<style>
  :root{
    --ice:#cfdeed;
    --royal:#0455a3;
    --mid:#3176b5;
    --sky:#85acd3;
    --navy:#06235e;
    --deep:#0a3a8c;
    --ink:#1d1d1f;
    --paper:#ffffff;
    --stage:#e7ebf0;
    --silver:#b9bec6;
  }
  *{margin:0;padding:0;box-sizing:border-box}
  html,body{width:1200px;height:2397px;overflow:hidden}
  body{background:var(--stage);position:relative;font-family:"Lora",Georgia,serif}

  .panel{position:absolute;width:480px;height:1079px;overflow:hidden;box-shadow:0 4px 18px rgba(0,0,0,.18)}
  .panel--left{left:75px}
  .panel--right{left:644px}
  .row-1{top:48px}
  .row-2{top:1243px}

  /* ---------- front ---------- */
  .front{background:var(--paper)}
  .front .sketch{position:absolute;left:16px;top:0;width:208px;height:304px;
    background:radial-gradient(ellipse at 50% 72%,#8d949e 0,#c8ccd2 28%,#eef0f3 60%,#fff 80%)}
  .logo-tab{position:absolute;left:307px;top:0;width:173px;height:189px;background:var(--royal);
    clip-path:polygon(0 0,100% 0,100% 80%,50% 100%,0 80%);display:flex;align-items:center;justify-content:center}
  .logo-name{font-family:"Cinzel",serif;font-weight:600;color:var(--paper);font-size:34px;letter-spacing:1px;text-transform:lowercase;margin-top:-24px}
  .trade-title{position:absolute;left:224px;top:214px;width:250px;text-align:center;
    font-family:"Cinzel",serif;color:var(--royal);font-size:31px;line-height:1.05}
  .service-band{position:absolute;left:0;top:323px;width:305px;height:82px;background:var(--royal);
    clip-path:polygon(0 0,100% 0,88% 100%,0 100%);padding:10px 0 0 8px;
    font-family:"Cinzel",serif;color:var(--paper);font-size:27px;line-height:1}
  .collage{position:absolute;left:0;top:405px;width:480px;height:560px;overflow:hidden}
  .tile{position:absolute;transform:rotate(-28deg);border:5px solid var(--paper)}
  .tile--blue{background:var(--royal)}
  .phone-bar{position:absolute;left:0;top:968px;width:480px;height:52px;background:var(--royal);
    font-family:"Cinzel",serif;color:var(--paper);font-size:40px;line-height:52px;padding-left:30px}
  .front-address{position:absolute;left:0;top:1028px;width:480px;text-align:center;
    font-family:"Cinzel",serif;color:var(--ink);font-size:19px}

  /* ---------- back ---------- */
  .back{background:linear-gradient(180deg,var(--navy) 0,var(--deep) 30%,var(--royal) 70%,var(--mid) 100%);
    color:var(--paper);text-align:center}
  .back .logo-box{position:absolute;left:170px;top:32px;width:140px;height:96px;
    display:flex;align-items:center;justify-content:center}
  .back .logo-name{margin:0;font-size:36px}
  .back-title{position:absolute;left:0;top:152px;width:100%;font-family:"Cinzel",serif;font-weight:700;font-size:29px;line-height:1}
  .back-title small{display:block;font-size:18px;margin-top:4px;font-weight:700}
  .tagline{position:absolute;left:0;top:234px;width:100%;font-family:"Cinzel",serif;font-size:10.5px;letter-spacing:.3px}
  .intro,.pitch{position:absolute;left:30px;width:420px;font-weight:700;font-size:13.4px;line-height:1.32}
  .intro{top:280px}
  .pitch{top:600px}
  .offer{position:absolute;left:0;top:421px;width:100%;height:144px;background:rgba(133,172,211,.45);padding-top:12px}
  .offer h2{font-family:"Cinzel",serif;font-weight:400;font-size:26px;line-height:1.2}
  .offer ul{list-style:none;font-size:17px;line-height:1.2;margin-top:6px}
  .steps{position:absolute;left:20px;top:752px;width:440px;display:flex;justify-content:space-between}
  .step{width:84px;display:flex;flex-direction:column;align-items:center}
  .step svg{width:56px;height:56px}
  .step p{font-size:9.4px;line-height:1.15;margin-top:6px}
  .contact{position:absolute;left:0;top:906px;width:340px;height:142px;background:rgba(133,172,211,.28);
    clip-path:polygon(0 0,92% 0,100% 50%,92% 100%,0 100%);text-align:left;padding:8px 0 0 24px}
  .contact h3{font-family:"Cinzel",serif;font-weight:400;font-size:22px;line-height:1;padding-left:30px}
  .contact .phones{font-family:"Cinzel",serif;font-size:22px;letter-spacing:3px;line-height:1.05;margin-top:2px;position:relative;padding-left:30px}
  .contact .line{display:flex;align-items:center;gap:12px;font-size:13px;font-weight:700;margin-top:7px}
  .contact svg{flex:none}
  .phones svg{position:absolute;left:0;top:4px}
  .seal{position:absolute;left:347px;top:935px;width:104px;height:110px}
</style>
</head>
<body>

<!-- ===== Version A ===== -->
<section class="panel panel--left row-1 front">
  <div class="sketch" role="img" aria-label="Line sketch of a solitaire ring above a rendered diamond ring"></div>
  <div class="logo-tab"><span class="logo-name">lv mfg</span></div>
  <h1 class="trade-title">Full Service<br>Trade Shop</h1>
  <div class="service-band">Repair, Design,<br>&amp; Casting</div>
  <div class="collage" role="img" aria-label="Collage of jewelry photos: bench work, an oval halo ring, casting flame, CAD screen and ring renders">
    <div class="tile" style="left:300px;top:-60px;width:210px;height:170px;background:linear-gradient(135deg,#7a5b3d,#c7a07a,#5c4634)"></div>
    <div class="tile" style="left:110px;top:-10px;width:200px;height:180px;background:radial-gradient(#f4f5f7,#b8bdc4)"></div>
    <div class="tile" style="left:-80px;top:90px;width:200px;height:200px;background:linear-gradient(135deg,#3a1d0c,#e8762a,#ffd27a)"></div>
    <div class="tile" style="left:190px;top:110px;width:230px;height:190px;background:radial-gradient(#ffffff,#a9aeb6)"></div>
    <div class="tile" style="left:30px;top:250px;width:220px;height:190px;background:linear-gradient(135deg,#1f3d7a,#4fa3b0,#d9dde2)"></div>
    <div class="tile" style="left:260px;top:330px;width:260px;height:260px;background:radial-gradient(#e9ebee,#7d838c)"></div>
    <div class="tile tile--blue" style="left:-70px;top:430px;width:160px;height:120px"></div>
  </div>
  <div class="phone-bar">1-888-555-0147</div>
  <p class="front-address">12 Heron Court Delhi, LA 71232</p>
</section>

<section class="panel panel--right row-1 back">
  <div class="logo-box"><span class="logo-name">lv mfg</span></div>
  <h1 class="back-title">LV Manufacturing<small>Manufacturing</small></h1>
  <p class="tagline">TOP QUALITY CRAFTSMANSHIP, FRIENDLY PERSONAL SERVICE</p>
  <p class="intro">We are a family operated business, serving the jewelry industry for over 45 years.<br>Our experience provides us with a vast knowledge of the industry,as well as best practices for each unique item.<br>We pride ourselves in quality craftsmanship with fast, honest, and courteous service.</p>
  <div class="offer">
    <h2>WHAT WE OFFER</h2>
    <ul>
      <li>Basic &amp; advanced jewelry repair</li>
      <li>Precision diamond setting</li>
      <li>CAD / CAM services for custom designs</li>
      <li>High Quality Gold, Silver, &amp; Platinum casting</li>
    </ul>
  </div>
  <p class="pitch">Lem Vossick Manufacturing can provide that highly skilled jeweler needed to take your business to the next level.<br>We will work directly with you to meet all your customer's needs, while maintaining a personal level of service that you will enjoy.<br>Our daily goal is to make you look good to your customer!</p>
  <div class="steps">
    <div class="step"><svg viewBox="0 0 56 56"><circle cx="28" cy="28" r="26" fill="#fff"/><rect x="16" y="20" width="24" height="18" fill="none" stroke="#0455a3" stroke-width="3"/><path d="M16 26h24" stroke="#0455a3" stroke-width="3"/></svg><p>You ship your item(s), with instructions for each job.</p></div>
    <div class="step"><svg viewBox="0 0 56 56"><circle cx="28" cy="28" r="26" fill="#fff"/><path d="M20 16l6 0 3 8-4 3c2 4 4 6 8 8l3-4 8 3v6c-14 0-24-10-24-24z" fill="#0455a3"/></svg><p>We receive your items and give you a call with any questions or concerns</p></div>
    <div class="step"><svg viewBox="0 0 56 56"><circle cx="28" cy="28" r="26" fill="#fff"/><path d="M18 29l7 7 13-15" fill="none" stroke="#0455a3" stroke-width="4"/></svg><p>Our Master Jewelers will provide the quality work</p></div>
    <div class="step"><svg viewBox="0 0 56 56"><circle cx="28" cy="28" r="26" fill="#fff"/><path d="M14 28h22M28 19l9 9-9 9" fill="none" stroke="#0455a3" stroke-width="4"/></svg><p>We ship your items back to you via your preferred shipping method</p></div>
    <div class="step"><svg viewBox="0 0 56 56"><circle cx="28" cy="28" r="26" fill="#fff"/><path d="M28 14l4 9 10 1-7 7 2 10-9-5-9 5 2-10-7-7 10-1z" fill="#0455a3"/></svg><p>You receive the package, inspect the work, and finish the sale.</p></div>
  </div>
  <div class="contact">
    <h3>CONTACT US</h3>
    <div class="phones"><svg width="22" height="22" viewBox="0 0 24 24"><path d="M5 3h4l2 5-3 2c1 3 3 5 6 6l2-3 5 2v4c-10 0-16-6-16-16z" fill="#fff"/></svg>888-555-0147<br>318-555-0192</div>
    <div class="line"><svg width="18" height="22" viewBox="0 0 18 22"><path d="M9 0a8 8 0 0 1 8 8c0 6-8 14-8 14S1 14 1 8a8 8 0 0 1 8-8z" fill="#fff"/><circle cx="9" cy="8" r="3" fill="#0455a3"/></svg>12 Heron Court Delhi, LA 71232</div>
    <div class="line"><svg width="18" height="14" viewBox="0 0 18 14"><rect width="18" height="14" rx="2" fill="#fff"/><path d="M1 2l8 6 8-6" fill="none" stroke="#0455a3" stroke-width="2"/></svg>owner@lvmfgshop.com</div>
  </div>
  <svg class="seal" viewBox="0 0 104 110" role="img" aria-label="Anniversary seal"><path d="M32 80l-8 28 14-8 8 10 6-26zM72 80l8 28-14-8-8 10-6-26z" fill="#c9ced6"/><circle cx="52" cy="50" r="48" fill="#dfe3e8"/><circle cx="52" cy="50" r="40" fill="#8e96a2"/><circle cx="52" cy="50" r="34" fill="#c9ced6"/></svg>
</section>

<!-- ===== Version B ===== -->
<section class="panel panel--left row-2 front">
  <div class="sketch" role="img" aria-label="Line sketch of a solitaire ring above a rendered diamond ring"></div>
  <div class="logo-tab"><span class="logo-name">lv mfg</span></div>
  <h1 class="trade-title">Full Service<br>Trade Shop</h1>
  <div class="service-band">Repair, Design,<br>&amp; Casting</div>
  <div class="collage" role="img" aria-label="Collage of jewelry photos: stacked gold rings, bench work, a halo ring, CAD screen and casting flame">
    <div class="tile" style="left:300px;top:-40px;width:210px;height:170px;background:radial-gradient(#f3e4c0,#b89454,#dfe2e6)"></div>
    <div class="tile" style="left:130px;top:60px;width:210px;height:170px;background:linear-gradient(135deg,#5c4634,#c7a07a,#7a5b3d)"></div>
    <div class="tile" style="left:-70px;top:130px;width:210px;height:180px;background:radial-gradient(#ffffff,#a9aeb6)"></div>
    <div class="tile tile--blue" style="left:330px;top:140px;width:180px;height:100px"></div>
    <div class="tile" style="left:230px;top:220px;width:220px;height:180px;background:linear-gradient(135deg,#1f3d7a,#4fa3b0,#d9dde2)"></div>
    <div class="tile" style="left:20px;top:330px;width:200px;height:190px;background:linear-gradient(135deg,#3a1d0c,#e8762a,#ffd27a)"></div>
    <div class="tile" style="left:270px;top:400px;width:240px;height:220px;background:radial-gradient(#e9ebee,#7d838c)"></div>
  </div>
  <div class="phone-bar">1-888-555-0147</div>
  <p class="front-address">12 Heron Court Delhi, LA 71232</p>
</section>

<section class="panel panel--right row-2 back">
  <div class="logo-box"><span class="logo-name">lv mfg</span></div>
  <h1 class="back-title">LV Manufacturing<small>Manufacturing</small></h1>
  <p class="tagline">TOP QUALITY CRAFTSMANSHIP, FRIENDLY PERSONAL SERVICE</p>
  <p class="intro">We are a family operated business, serving the jewelry industry for over 45 years.<br>Our experience provides us with a vast knowledge of the industry,as well as best practices for each unique item.<br>We pride ourselves in quality craftsmanship with fast, honest, and courteous service.</p>
  <div class="offer">
    <h2>WHAT WE OFFER</h2>
    <ul>
      <li>Basic &amp; advanced jewelry repair</li>
      <li>Precision diamond setting</li>
      <li>CAD / CAM services for custom designs</li>
      <li>High Quality Gold, Silver, &amp; Platinum casting</li>
    </ul>
  </div>
  <p class="pitch">Lem Vossick Manufacturing can provide that highly skilled jeweler needed to take your business to the next level.<br>We will work directly with you to meet all your customer's needs, while maintaining a personal level of service that you will enjoy.<br>Our daily goal is to make you look good to your customer!</p>
  <div class="steps">
    <div class="step"><svg viewBox="0 0 56 56"><circle cx="28" cy="28" r="26" fill="#fff"/><rect x="16" y="20" width="24" height="18" fill="none" stroke="#0455a3" stroke-width="3"/><path d="M16 26h24" stroke="#0455a3" stroke-width="3"/></svg><p>You ship your item(s), with instructions for each job.</p></div>
    <div class="step"><svg viewBox="0 0 56 56"><circle cx="28" cy="28" r="26" fill="#fff"/><path d="M20 16l6 0 3 8-4 3c2 4 4 6 8 8l3-4 8 3v6c-14 0-24-10-24-24z" fill="#0455a3"/></svg><p>We receive your items and give you a call with any questions or concerns</p></div>
    <div class="step"><svg viewBox="0 0 56 56"><circle cx="28" cy="28" r="26" fill="#fff"/><path d="M18 29l7 7 13-15" fill="none" stroke="#0455a3" stroke-width="4"/></svg><p>Our Master Jewelers will provide the quality work</p></div>
    <div class="step"><svg viewBox="0 0 56 56"><circle cx="28" cy="28" r="26" fill="#fff"/><path d="M14 28h22M28 19l9 9-9 9" fill="none" stroke="#0455a3" stroke-width="4"/></svg><p>We ship your items back to you via your preferred shipping method</p></div>
    <div class="step"><svg viewBox="0 0 56 56"><circle cx="28" cy="28" r="26" fill="#fff"/><path d="M28 14l4 9 10 1-7 7 2 10-9-5-9 5 2-10-7-7 10-1z" fill="#0455a3"/></svg><p>You receive the package, inspect the work, and finish the sale.</p></div>
  </div>
  <div class="contact">
    <h3>CONTACT US</h3>
    <div class="phones"><svg width="22" height="22" viewBox="0 0 24 24"><path d="M5 3h4l2 5-3 2c1 3 3 5 6 6l2-3 5 2v4c-10 0-16-6-16-16z" fill="#fff"/></svg>888-555-0147<br>318-555-0192</div>
    <div class="line"><svg width="18" height="22" viewBox="0 0 18 22"><path d="M9 0a8 8 0 0 1 8 8c0 6-8 14-8 14S1 14 1 8a8 8 0 0 1 8-8z" fill="#fff"/><circle cx="9" cy="8" r="3" fill="#0455a3"/></svg>12 Heron Court Delhi, LA 71232</div>
    <div class="line"><svg width="18" height="14" viewBox="0 0 18 14"><rect width="18" height="14" rx="2" fill="#fff"/><path d="M1 2l8 6 8-6" fill="none" stroke="#0455a3" stroke-width="2"/></svg>owner@lvmfgshop.com</div>
  </div>
  <svg class="seal" viewBox="0 0 104 110" role="img" aria-label="Anniversary seal"><path d="M32 80l-8 28 14-8 8 10 6-26zM72 80l8 28-14-8-8 10-6-26z" fill="#c9ced6"/><circle cx="52" cy="50" r="48" fill="#dfe3e8"/><circle cx="52" cy="50" r="40" fill="#8e96a2"/><circle cx="52" cy="50" r="34" fill="#c9ced6"/></svg>
</section>

</body>
</html>
```